Belvascotravel.com web design project + logo design

Hi,

We are a Russian online tour operator - sunkettle.com

We are looking to tranmsfer our domain to belvascotravel.com. The website and logo need to be belvascoesque - we are not looking to change our functionality, but we need to make the website much more attracitve to clients, much more wild looking but at the same time remaining a professional travel company.

The main concept of the website should be innovative travel (as belvasco was an innovator). Alternatively, you could go down the artist route and go down the draw / design your own tour road.

On our website the customer is able to combine travel services (hotels, flights, Visa services, and soon chauffeur, car rental etc...) put it into their basket (the basket definitely has to look better than it is at the moment) and pay for it in one go by card.

We are also stressin our customer support with web chat, call centre etc... (call centre number at the top of the page)

We aim to provide an easy user experience, but we need to make it have some more style, so I will be waiting for what you guys can come up with.
Let me know if you have any questions - skype is: mrdolbarin

Industry/Entity Type

It Company

Requirements
Must have
• It is quite a simple task - to take the existing website sunkettle.com and belvascosize it to create belvascotravel.com, the functionality of the website will remain the same and there are not many pages in the website. Homepage, Checkout step1, Checkout step 2 (you can view both of these if you select a service) and the generic pages for T&C''s, Privacy policy etc...

IMPORTANT UPDATE

We are also looking at how the search results will look in the designs, (please do a search on our website for hotel / flight)

```html
<!DOCTYPE html>
<html lang="en">
<head>
<meta charset="utf-8">
<title>Belvasco Travel</title>
<link rel="stylesheet" href="https://fonts.googleapis.com/css2?family=Roboto:wght@300;400;500&display=swap">
<style>
:root{
  --dark:#3a3a3a;
  --darker:#2e2e2e;
  --pink:#ee2b8f;
  --blue:#19b5f1;
  --grey-bg:#ebebeb;
  --hero:#d5d5d5;
  --field:#dcdcdc;
  --text:#444;
  --muted:#777;
  --white:#fff;
}
*{box-sizing:border-box;margin:0;padding:0}
html,body{width:756px;height:1200px;overflow:hidden}
body{font-family:"Roboto",Arial,sans-serif;color:var(--text);background:var(--white);position:relative}
.abs{position:absolute;white-space:nowrap}

/* header */
.site-header{left:0;top:0;width:756px;height:62px;background:var(--dark)}
.brand{left:126px;top:14px;display:flex;align-items:center;gap:8px}
.brand-dot{width:30px;height:30px;border-radius:50%;background:var(--white)}
.brand-name{color:var(--white);font-size:21px;font-weight:400;line-height:1}
.lang{left:592px;top:12px;width:40px;height:10px;background:#e6e6e6;font-size:6px;color:#333;padding-left:3px;line-height:10px}
.lang::after{content:"";position:absolute;right:1px;top:1px;width:8px;height:8px;background:var(--dark)}
.phone{left:490px;top:26px;display:flex;gap:6px;align-items:flex-start}
.phone-number{color:var(--white);font-size:16px;font-weight:300;line-height:1}
.phone-hours{color:var(--pink);font-size:7px;margin-top:2px}

/* hero */
.hero{left:0;top:62px;width:756px;height:304px;background:var(--hero)}
.hero-art{left:126px;top:6px;width:506px;height:122px;background:linear-gradient(180deg,#dedede,#cfcfcf)}
.side-btn{left:584px;width:46px;height:17px;background:#f2f2f2;border:1px solid #c6c6c6;font-size:6.5px;color:var(--pink);display:flex;align-items:center;gap:4px;padding-left:4px;white-space:nowrap}
.side-btn i{width:7px;height:7px;background:var(--dark);display:block;border-radius:50%;flex:none}

.tabs{left:126px;top:110px;display:flex;gap:2px}
.tab{width:56px;height:18px;background:#555;color:#ccc;font-size:7px;text-align:center;line-height:19px}
.tab.is-active{background:var(--blue);color:var(--white)}
.booking{left:126px;top:128px;width:372px;height:128px;background:var(--white)}
.lbl{font-size:7.5px;color:var(--pink)}
.field{height:14px;border:2px solid var(--field);font-size:6px;color:#aaa;padding-left:3px;line-height:10px;background:var(--white)}
.field.val{color:#555}
.sel{width:23px;height:14px;border:2px solid var(--field);font-size:6px;color:#333;padding-left:3px;line-height:10px}
.sel::after{content:"";position:absolute;right:1px;top:1px;width:8px;height:8px;background:var(--dark)}
.mini{font-size:5px;color:#aaa}
.btn-search{left:149px;top:96px;width:74px;height:22px;background:var(--dark);color:var(--white);font-size:11px;font-weight:300;text-align:center;line-height:22px;border-bottom:2px solid #222}

.basket{left:502px;top:129px;width:128px;height:127px;background:var(--white)}
.basket-head{left:0;top:0;width:128px;height:19px;background:var(--blue);color:var(--dark);font-size:12px;text-align:center;line-height:20px}
.basket-pay{left:0;top:72px;width:128px;height:18px;background:var(--pink);color:var(--white);font-size:8px;text-align:center;line-height:18px}
.cards{left:16px;top:94px;display:flex;gap:4px}
.cards span{width:17px;height:10px;background:#cfd6dc;border:1px solid #bbb;display:block}
.pricing{left:0;top:110px;width:128px;height:17px;background:#555;color:var(--white);font-size:7.5px;text-align:center;line-height:17px}

.quick{left:304px;top:274px;width:148px;height:32px;background:var(--white);text-align:center;font-size:8.5px;font-weight:300;color:#222;padding-top:3px}
.btn-pink{display:inline-block;margin-top:2px;background:var(--pink);color:var(--white);font-size:8px;padding:2px 6px}

/* search band */
.search-band{left:0;top:366px;width:756px;height:94px;background:linear-gradient(180deg,#fff 20%,#e4e4e4)}
.search-band::after{content:"";position:absolute;left:0;bottom:0;width:756px;height:2px;background:var(--blue)}
.step{height:12px;background:var(--blue);color:#114;font-size:6px;line-height:12px;padding:0 5px}
.chk{font-size:5.5px;color:#444;display:flex;align-items:center;gap:5px}
.chk i{width:7px;height:6px;border:1px solid #bbb;background:#fff;display:block}
.input-sm{height:14px;border:1px solid #ccc;background:#fff;font-size:5.5px;color:#999;line-height:12px;padding-left:3px}
.cal{right:2px;top:2px;width:8px;height:8px;border:1px solid #555}
.spin{width:38px;height:15px;border:1px solid #ccc;background:#fff;font-size:6px;line-height:13px;padding-left:4px}
.btn-dark{background:var(--dark);color:var(--white);text-align:center}

/* sections */
.tag{height:23px;background:#555;color:var(--white);font-size:14px;font-weight:300;padding:0 8px;line-height:24px}
.section-title{color:var(--pink);font-weight:300;text-align:center;white-space:nowrap}
.info{left:0;top:480px;width:756px;height:198px;background:var(--grey-bg)}
.option{font-size:11.5px;color:#222;text-align:center;width:200px}
.btn-blue{width:54px;height:18px;background:var(--blue);color:var(--white);font-size:7.5px;text-align:center;line-height:18px}

.tickets{left:0;top:678px;width:756px;height:220px;background:var(--white)}
.tickets-art{left:126px;top:2px;width:506px;height:202px;background:linear-gradient(180deg,#f6f6f8,#ececef)}
.title-box{background:var(--white);border:1px solid #ddd}
.text-box{background:var(--white);border:1px solid #ddd;font-size:6.5px;line-height:11px;color:#555;padding:5px 9px;white-space:normal}

.hotels{left:0;top:898px;width:756px;height:164px;background:var(--grey-bg)}
.body-copy{font-size:6.5px;line-height:11px;color:#555;white-space:normal}

/* footer */
.footer{left:0;top:1096px;width:756px;height:84px;background:var(--blue)}
.offers{left:474px;top:1076px;width:158px;height:44px;background:var(--white)}
.offers h4{font-size:8.5px;font-weight:500;color:#222;position:absolute;left:7px;top:6px}
.email{left:8px;top:22px;width:142px;height:15px;background:var(--pink);border-radius:8px;color:#ffd3ea;font-size:5.5px;line-height:15px;padding-left:6px}
.email b{position:absolute;right:0;top:0;width:42px;height:15px;background:#111;color:#fff;border-radius:8px;text-align:center;font-weight:400;font-size:6.5px}
.fcol h5{font-size:8px;font-weight:400;color:#173b55;margin-bottom:10px}
.fcol li{list-style:none;font-size:5.5px;color:var(--white);line-height:10px;display:flex;align-items:center;gap:4px}
.fcol li i{width:6px;height:6px;border-radius:50%;background:var(--white);display:block}
.foot-brand{left:528px;top:1134px;display:flex;align-items:center;gap:6px}
.foot-brand .brand-dot{width:26px;height:26px}
.foot-brand .brand-name{font-size:16px}
.bottom-bar{left:0;top:1180px;width:756px;height:20px;background:var(--darker);color:#ccc;font-size:5.5px;text-align:center;line-height:20px}
</style>
</head>
<body>

<header class="abs site-header">
  <div class="abs brand"><span class="brand-dot"></span><span class="brand-name">Belvasco Travel</span></div>
  <div class="abs lang">English</div>
  <div class="abs phone">
    <svg width="20" height="22" viewBox="0 0 20 22"><path d="M4 1l4 5-2 3c1 3 4 6 7 7l3-2 4 4-3 3C8 21-1 11 1 4z" fill="var(--pink)"/></svg>
    <div><div class="phone-number">8-800-555-0142</div><div class="phone-hours">(Mon-Fri) Hours: 9:00 am - 18:00</div></div>
  </div>
</header>

<section class="abs hero">
  <div class="abs hero-art" role="img" aria-label="Sketched world landmarks with a passenger plane"></div>
  <div class="abs side-btn" style="top:6px"><i></i>My Tour</div>
  <div class="abs side-btn" style="top:30px"><i></i>Web Chat</div>

  <div class="abs tabs">
    <div class="tab is-active">TICKETS</div><div class="tab">INFO</div><div class="tab">HOTELS</div>
  </div>

  <form class="abs booking">
    <span class="abs lbl" style="left:10px;top:17px">Whence</span>
    <div class="abs field" style="left:59px;top:13px;width:105px">Type...</div>
    <span class="abs lbl" style="left:182px;top:16px">Where</span>
    <div class="abs field" style="left:225px;top:13px;width:105px">Type...</div>

    <span class="abs lbl" style="left:10px;top:38px">There</span>
    <div class="abs field val" style="left:59px;top:35px;width:105px">30-5-2013</div>
    <span class="abs lbl" style="left:182px;top:39px">Back</span>
    <div class="abs field val" style="left:225px;top:35px;width:61px">16-6-2013</div>
    <div class="abs chk" style="left:292px;top:34px"><i style="background:#ccc"></i>Back</div>
    <div class="abs chk" style="left:292px;top:43px"><i style="background:#eee"></i>One way</div>

    <span class="abs mini" style="left:66px;top:55px">Men</span>
    <span class="abs mini" style="left:103px;top:55px">Women</span>
    <span class="abs mini" style="left:141px;top:55px">Children</span>
    <span class="abs lbl" style="left:10px;top:67px">Passengers</span>
    <div class="abs sel" style="left:59px;top:63px">1</div>
    <div class="abs sel" style="left:100px;top:63px">1</div>
    <div class="abs sel" style="left:140px;top:63px">1</div>
    <span class="abs lbl" style="left:182px;top:66px">Class</span>
    <div class="abs sel" style="left:225px;top:62px;width:105px">Economy</div>

    <div class="abs btn-search">Search</div>
  </form>

  <aside class="abs basket">
    <div class="abs basket-head">BASKET</div>
    <svg class="abs" style="left:38px;top:24px" width="52" height="44" viewBox="0 0 52 44">
      <circle cx="4" cy="4" r="3" fill="var(--blue)"/>
      <path d="M4 4l6 4 4 22h28l6-18H12" fill="none" stroke="#999" stroke-width="2"/>
      <path d="M14 16h32M16 23h28M22 12v18M30 12v18M38 12v18" stroke="#bbb" stroke-width="1"/>
      <circle cx="18" cy="38" r="4" fill="none" stroke="var(--dark)" stroke-width="2"/>
      <circle cx="38" cy="38" r="4" fill="none" stroke="var(--dark)" stroke-width="2"/>
    </svg>
    <div class="abs basket-pay">Payment</div>
    <div class="abs cards"><span></span><span></span><span></span><span></span><span></span></div>
    <div class="abs pricing">*Pricing</div>
  </aside>

  <div class="abs quick">Search for A Hotel / Flight<br><span class="btn-pink">Book Now</span></div>
</section>

<section class="abs search-band">
  <div class="abs step" style="left:126px;top:18px">01. What?</div>
  <div class="abs chk" style="left:126px;top:36px"><i></i>Hotels</div>
  <div class="abs chk" style="left:126px;top:50px"><i></i>Flights</div>
  <div class="abs chk" style="left:126px;top:64px"><i></i>Cars</div>

  <div class="abs step" style="left:213px;top:18px">02. Where?</div>
  <div class="abs input-sm" style="left:213px;top:36px;width:131px">Lorem Ipsum Dolor<span class="abs cal" style="background:var(--dark);border:0"></span></div>

  <div class="abs step" style="left:397px;top:18px">03. When?</div>
  <div class="abs input-sm" style="left:397px;top:36px;width:58px">Check In<span class="abs cal"></span></div>
  <div class="abs input-sm" style="left:397px;top:56px;width:58px">Check Out<span class="abs cal"></span></div>

  <div class="abs step" style="left:506px;top:18px">04. Who?</div>
  <span class="abs" style="left:506px;top:36px;font-size:6.5px">Rooms</span>
  <span class="abs" style="left:550px;top:36px;font-size:6.5px">Adults</span>
  <span class="abs" style="left:593px;top:36px;font-size:6.5px">Child</span>
  <div class="abs spin" style="left:506px;top:46px">01</div>
  <div class="abs spin" style="left:550px;top:46px">01</div>
  <div class="abs spin" style="left:593px;top:46px">01</div>

  <div class="abs btn-dark" style="left:570px;top:80px;width:62px;height:18px;font-size:8px;line-height:18px">Search</div>
</section>

<section class="abs info">
  <div class="abs tag" style="left:126px;top:12px">INFO</div>
  <h2 class="abs section-title" style="left:0;top:40px;width:756px;font-size:25px">There are two option apply for visa</h2>
  <p class="abs option" style="left:177px;top:94px">1. Oformlenie visa “Online”</p>
  <p class="abs option" style="left:408px;top:94px">2. Visa “Myself.”</p>
  <svg class="abs" style="left:267px;top:125px" width="20" height="28" viewBox="0 0 20 28"><path d="M7 0h6v16h7L10 28 0 16h7z" fill="#111"/></svg>
  <svg class="abs" style="left:498px;top:125px" width="20" height="28" viewBox="0 0 20 28"><path d="M7 0h6v16h7L10 28 0 16h7z" fill="#111"/></svg>
  <div class="abs btn-blue" style="left:250px;top:163px">Click Here</div>
  <div class="abs btn-blue" style="left:481px;top:163px">Click Here</div>
</section>

<section class="abs tickets">
  <div class="abs tickets-art" role="img" aria-label="Faint pastel sketch of city landmarks and a plane"></div>
  <div class="abs tag" style="left:126px;top:12px">TICKETS</div>
  <div class="abs title-box" style="left:226px;top:77px;width:306px;height:37px">
    <h2 class="section-title" style="font-size:22px;letter-spacing:-0.4px;line-height:35px">Flights from Tours designer.</h2>
  </div>
  <div class="abs text-box" style="left:126px;top:128px;width:506px;height:44px">On our site you can consider offers from different airlines and purchase tickets according to your wishes and budget. Plan dates of departures and arrivals c in any country, filling the cells you want, Tour Designer automatically displays your program in the calendar. On Tour Designer You can create any tour, including round-the-world and pay for all the services a single payment.</div>
</section>

<section class="abs hotels">
  <div class="abs tag" style="left:126px;top:10px">HOTELS</div>
  <h2 class="abs section-title" style="left:0;top:48px;width:756px;font-size:25px">Hotels by City Builder.</h2>
  <p class="abs body-copy" style="left:126px;top:99px;width:500px">Our site offers a wide selection of hotels located in different countries and continents of the world. You can choose and book all kinds of accommodation options, according to your wishes and budget. pursue their dreams! We have created for you the most convenient framework for planning a vacation or business trip. Tour Builder saves your time now to buy a package tour you can just 3 simple steps: Choose the services Confirm requested services, payment of a single payment. A complete set of documents confirming the purchase tour package will be on our website in your personal account, send documents to "Print".</p>
</section>

<footer class="abs footer">
  <div class="abs fcol" style="left:126px;top:14px"><h5>View Site</h5><ul><li>Home</li><li>About Us</li><li>Form</li><li>Contacts</li></ul></div>
  <div class="abs fcol" style="left:190px;top:14px"><h5>Follow Us</h5><ul><li style="line-height:13px"><i></i>Pagebook</li><li style="line-height:13px"><i></i>Chirper</li><li style="line-height:13px"><i></i>Blog</li></ul></div>
  <div class="abs fcol" style="left:263px;top:14px"><h5>Contact Us</h5><ul><li><svg width="6" height="6" viewBox="0 0 6 6"><path d="M1 0l2 2-1 1 1 1 1-1 2 2-1 1C2 6 0 4 0 1z" fill="#fff"/></svg>+7 (495) 555-01-27</li><li><svg width="6" height="6" viewBox="0 0 6 6"><path d="M1 0l2 2-1 1 1 1 1-1 2 2-1 1C2 6 0 4 0 1z" fill="#fff"/></svg>8-800-555-0142</li><li><svg width="6" height="5" viewBox="0 0 6 5"><rect width="6" height="5" fill="#fff"/></svg>info@belvascotravel.com</li></ul></div>
  <div class="abs fcol" style="left:366px;top:14px"><h5>Find Us</h5><ul><li>Tour Builder Limited 14</li><li>Harrow Lane Leeds,</li><li>LS2 7QT UK</li></ul></div>
</footer>
<div class="abs offers"><h4>Exclusive Offers</h4><div class="abs email">Email Address<b>Send</b></div></div>
<div class="abs foot-brand"><span class="brand-dot"></span><span class="brand-name">Belvasco Travel</span></div>
<div class="abs bottom-bar">© 2012–2013 BelvascoTravel, Terms &amp; Conditions : Privacy Policy</div>

</body>
</html>
```